Software Development Consulting Company Needs Business Card Design

We need a new business card design for our consultants at Kestrel Works (kestrelworks.example). We are a small firm that provides high-end software development and methodology consulting to medium to large enterprise IT organizations.

Our logo uses Futura for the font and we would like to stick with navy blue and canary yellow for the logo colors. Attached are normal and reversed versions of our logos in illustrator format.
Updates

Hi Everyone, Thank yo very much for your amazing design ideas. I have created a poll for this project and our employees will be voting on the design they wish to use. We will be making a decision this Wednesday (October 22nd). Thanks again, Dale Hartwick

Industry/Entity Type

Business

```html
<!DOCTYPE html>
<html lang="en">
<head>
<meta charset="utf-8">
<title>Kestrel Works — Business Card</title>
<link rel="stylesheet" href="https://fonts.googleapis.com/css2?family=Jost:wght@400;500&family=Open+Sans:wght@400;600;700&display=swap">
<style>
  :root {
    --navy: #1d4a6e;
    --navy-deep: #173e5e;
    --canary: #f3e21a;
    --paper: #ffffff;
    --ink-soft: #5b6570;
    --rule: #c9ced4;
    --backdrop: #eceae6;
  }
  * { box-sizing: border-box; margin: 0; padding: 0; }
  html, body { width: 1200px; height: 720px; overflow: hidden; }
  body {
    background: var(--backdrop);
    display: flex;
    align-items: center;
    justify-content: center;
    gap: 40px;
    font-family: "Open Sans", Arial, sans-serif;
  }
  .card {
    position: relative;
    width: 540px;
    height: 309px;
    overflow: hidden;
    box-shadow: 0 6px 18px rgba(0,0,0,0.18);
  }
  /* Front */
  .card--front { background: var(--paper); }
  .card__wave { position: absolute; inset: 0; width: 100%; height: 100%; }
  .brand {
    display: flex;
    align-items: center;
    gap: 10px;
    font-family: "Jost", "Futura", sans-serif;
    font-weight: 500;
    text-transform: uppercase;
    letter-spacing: 0.12em;
  }
  .brand__dot {
    width: 14px; height: 14px;
    border-radius: 50%;
    background: var(--canary);
    flex: none;
  }
  .card--front .brand {
    position: absolute;
    left: 34px;
    top: 104px;
    font-size: 25px;
    color: var(--navy);
  }
  .card__divider {
    position: absolute;
    left: 296px;
    top: 22px;
    width: 1px;
    height: 118px;
    background: var(--rule);
  }
  .contact {
    position: absolute;
    left: 318px;
    top: 24px;
    color: var(--navy);
  }
  .contact__name { font-size: 17px; font-weight: 700; line-height: 1.15; }
  .contact__title { font-size: 11px; color: var(--ink-soft); margin-bottom: 10px; }
  .contact__line {
    display: flex;
    align-items: center;
    gap: 5px;
    font-size: 11.5px;
    line-height: 1.5;
    color: var(--navy-deep);
  }
  .contact__line svg { width: 11px; height: 11px; fill: var(--navy); flex: none; }
  .card__url {
    position: absolute;
    right: 26px;
    bottom: 18px;
    font-size: 13px;
    letter-spacing: 0.08em;
    color: var(--paper);
  }
  /* Back */
  .card--back { background: var(--navy); }
  .card--back .brand {
    position: absolute;
    left: 0; right: 0;
    top: 102px;
    justify-content: center;
    font-size: 34px;
    color: var(--paper);
  }
  .card--back .brand__dot { width: 18px; height: 18px; }
  .card--back .card__url {
    left: 0; right: 0;
    bottom: 58px;
    text-align: center;
    font-size: 17px;
    letter-spacing: 0.12em;
  }
</style>
</head>
<body>

  <section class="card card--front" aria-label="Business card front">
    <svg class="card__wave" viewBox="0 0 540 309" preserveAspectRatio="none" aria-hidden="true">
      <path d="M0 254 C150 250 320 220 540 150 L540 162 C330 230 160 264 0 270 Z" fill="var(--canary)"/>
      <path d="M140 256 C300 244 420 206 540 144 L540 149 C420 210 300 248 140 256 Z" fill="var(--navy)"/>
      <path d="M0 274 C170 270 340 238 540 166 L540 309 L0 309 Z" fill="var(--navy)"/>
    </svg>

    <div class="brand"><span class="brand__dot"></span>Kestrel Works</div>

    <div class="card__divider"></div>

    <div class="contact">
      <p class="contact__name">Your Name</p>
      <p class="contact__title">Title</p>
      <p class="contact__line">
        <svg viewBox="0 0 24 24" aria-hidden="true"><path d="M6.6 10.8a15.2 15.2 0 0 0 6.6 6.6l2.2-2.2a1 1 0 0 1 1-.25 11.4 11.4 0 0 0 3.6.57 1 1 0 0 1 1 1V20a1 1 0 0 1-1 1A17 17 0 0 1 3 4a1 1 0 0 1 1-1h3.5a1 1 0 0 1 1 1c0 1.25.2 2.45.57 3.57a1 1 0 0 1-.25 1z"/></svg>
        555-010-0199
      </p>
      <p class="contact__line">
        <svg viewBox="0 0 24 24" aria-hidden="true"><path d="M2 5h20v14H2z M4 7v.5l8 5 8-5V7l-8 5z" fill-rule="evenodd"/></svg>
        info@kestrelworks.example
      </p>
      <p class="contact__line">Northgate + Riverton, IL</p>
    </div>

    <p class="card__url">www.kestrelworks.example</p>
  </section>

  <section class="card card--back" aria-label="Business card back">
    <div class="brand"><span class="brand__dot"></span>Kestrel Works</div>
    <p class="card__url">www.kestrelworks.example</p>
  </section>

</body>
</html>
```